Moravel Aesthetic Doctor

I require an elegant, luxurious looking business card for my aesthetic business. I am a doctor and that will set me aside from competitors. I am planning to provide home and spa based treatments to clients with high expectations. I have attached my logo.

```html
<!DOCTYPE html>
<html lang="en">
<head>
<meta charset="utf-8">
<title>Moravel Aesthetic Doctor – Business Card</title>
<link href="https://fonts.googleapis.com/css2?family=Quicksand:wght@400;500;600&display=swap" rel="stylesheet">
<style>
  :root {
    --backdrop: #2bb4e6;
    --card: #ffffff;
    --ink: #2e3338;
    --accent: #29a9e1;
    --mark-grey: #a7a9ac;
    --shadow: rgba(10, 70, 110, 0.25);
  }
  * { margin: 0; padding: 0; box-sizing: border-box; }
  html, body {
    width: 1200px;
    height: 800px;
    overflow: hidden;
    background: var(--backdrop);
    font-family: "Quicksand", sans-serif;
  }
  .canvas {
    width: 1200px;
    height: 800px;
    display: flex;
    align-items: center;
    justify-content: center;
    gap: 60px;
  }
  .card {
    width: 520px;
    height: 320px;
    background: var(--card);
    border-radius: 28px;
    box-shadow: 0 18px 40px var(--shadow);
    position: relative;
    overflow: hidden;
  }

  /* Front: brand name and tagline */
  .card-front {
    display: flex;
    flex-direction: column;
    align-items: center;
    justify-content: center;
    gap: 18px;
  }
  .brand {
    display: flex;
    align-items: center;
    gap: 16px;
  }
  .brand-dot {
    width: 46px;
    height: 46px;
    border-radius: 50%;
    background: var(--accent);
    flex: none;
  }
  .brand-name {
    font-weight: 500;
    font-size: 30px;
    color: var(--accent);
    letter-spacing: 0.06em;
    text-transform: uppercase;
    line-height: 1.15;
  }
  .tagline {
    font-size: 17px;
    font-weight: 500;
    color: var(--ink);
    letter-spacing: 0.02em;
  }

  /* Back: contact details */
  .card-back {
    padding: 38px 44px;
    display: flex;
    flex-direction: column;
    justify-content: center;
  }
  .card-back .brand { margin-bottom: 22px; }
  .card-back .brand-dot { width: 30px; height: 30px; }
  .card-back .brand-name { font-size: 19px; }
  .doctor-name {
    font-size: 17px;
    font-weight: 600;
    color: var(--ink);
  }
  .doctor-name .postnominals {
    font-size: 10px;
    font-weight: 500;
    letter-spacing: 0.04em;
    margin-left: 4px;
  }
  .qualification {
    font-size: 13px;
    font-weight: 500;
    color: var(--accent);
    margin-top: 4px;
  }
  .divider {
    width: 14px;
    height: 2px;
    background: var(--accent);
    margin: 12px 0;
  }
  .contact-list {
    list-style: none;
    font-size: 14px;
    font-weight: 500;
    color: var(--ink);
    line-height: 1.6;
  }
  .contact-list .web-name { color: var(--accent); }
  .social-row {
    display: flex;
    gap: 8px;
    margin-top: 10px;
  }
  .social-dot {
    width: 14px;
    height: 14px;
    border-radius: 50%;
    background: var(--accent);
  }
</style>
</head>
<body>
  <main class="canvas">
    <section class="card card-front" aria-label="Card front">
      <div class="brand">
        <span class="brand-dot" aria-hidden="true"></span>
        <span class="brand-name">Moravel<br>Aesthetic Doctor</span>
      </div>
      <p class="tagline">Home and Spa Based Treatments</p>
    </section>

    <section class="card card-back" aria-label="Card back">
      <div class="brand">
        <span class="brand-dot" aria-hidden="true"></span>
        <span class="brand-name">Moravel Aesthetic Doctor</span>
      </div>
      <p class="doctor-name">Dr.Elise Varnholt<span class="postnominals">MRCPCH MD</span></p>
      <p class="qualification">Australasian Diploma of Aesthetic Medicine</p>
      <span class="divider" aria-hidden="true"></span>
      <ul class="contact-list">
        <li>0800 555 014</li>
        <li>elise@moravel.co.nz</li>
        <li>www.<span class="web-name">moravel</span>.co.nz</li>
      </ul>
      <div class="social-row" aria-label="Social channels">
        <span class="social-dot"></span>
        <span class="social-dot"></span>
      </div>
    </section>
  </main>
</body>
</html>
```